Spanish Student Needs a Cover for his PhD Dissertation

Hi everyone :) So, I'm a Corneal surgeon currently finishing my PhD, with a dissertation focused on the evaluation of quality of life in patients affected by a disease called Keratoconus. Just so you know, Keratoconus is a condition in which the cornea (the frontal part of the way) gets thin and bulgy and it decreases vision. What I did during my PhD was designing a questionnaire for evaluating quality of life in this kind of patients.
I need to design a hard cover for my dissertation, which is 200 sheets long. I like kind of minimalistic and geometric designs but I am totally open to suggestions. What needs to be in the cover is the name of the dissertation "Diseño, desarrollo y validación de una encuesta para evaluar el compromiso visual y emocional subjetivos en pacientes con Queratocono" and my name, "Iker Zurmendi". The other thing that needs to go there is the logo of my university (Universidad de Montehierro). Aside from that, anything else is up to the designer. It would be important to use the kind of "red" color I am using in the dissertation. I am attaching the frontal page of my dissertation so you know what kind of design and colors I am using.
In the back part, of the cover, there should be this small inscription: "Iker Zurmendi, MD, es un Oftalmólogo Subespecialista en Cirugía Refractiva de la Universidad Tecnológica Cordillerana (Colombia) y la Universidad de Montehierro (España). Actualmente se desempeña como miembro del Departamento de Córnea y Cirugía Refractiva de la Clínica de Oftalmología Miraluz y como director de su propia compañía de emprendimiento médico Silver Heron Surgical". Please leave a space to place my picture; I will have it taken this week so I don't have it right now, you can just leave the blank spot and I will include it later
The size of the pages is standard "letter" size.
Thanks a lot!

Target Market(s)

PhD Scholars

Font styles to use
Serif

Requirements
Must have
• The "red" color I use on my font. It must be formal but "young".
Nice to have
• I like to keep the design clean, kind of "formal with a young" touch so to speak. I really like gray colors, so it would be nice to have broad areas of gray. I love geometrical designs.
I have uploaded a very early version a friend of mine made (it even had a different title); this can be a starting point for you to work on, but I am more than open to suggestions and new ideas.
Should not have
• Please don't use my whole name, Iker Zurmendi is fine. I don't like ALL CAPITALS.

```html
<!DOCTYPE html>
<html lang="es">
<head>
<meta charset="utf-8">
<title>Cubierta de tesis doctoral – Iker Zurmendi</title>
<link rel="stylesheet" href="https://fonts.googleapis.com/css2?family=Noto+Serif:wght@400;700&family=Montserrat:wght@600;700&family=Crimson+Text&family=Roboto:wght@700&display=swap">
<style>
  :root {
    --crimson: #ad1f43;
    --charcoal: #252525;
    --slate: #858585;
    --paper: #ffffff;
    --ink: #1a1a1a;
    --iris-amber: #b5722e;
    --iris-green: #6f7a45;
    --skin-rose: #e7c9c4;
  }
  html, body {
    margin: 0;
    padding: 0;
    width: 1200px;
    height: 930px;
    overflow: hidden;
    background: var(--paper);
  }
  .cover-sheet {
    display: block;
    width: 1200px;
    height: 930px;
  }
  .view-label {
    font-family: "Noto Serif", serif;
    font-size: 38px;
    fill: var(--crimson);
    text-anchor: middle;
  }
  .thesis-title {
    font-family: "Noto Serif", serif;
    font-weight: 700;
    font-size: 41px;
    letter-spacing: 1px;
    fill: var(--paper);
    text-anchor: end;
  }
  .university-line {
    font-family: "Montserrat", sans-serif;
    font-weight: 600;
    font-size: 33px;
    letter-spacing: 1.5px;
    fill: var(--paper);
    text-anchor: end;
  }
  .author-name {
    font-family: "Montserrat", sans-serif;
    font-weight: 700;
    font-size: 46px;
    letter-spacing: 5px;
    fill: var(--paper);
    text-anchor: middle;
  }
  .crest-name {
    font-family: "Roboto", sans-serif;
    font-weight: 700;
    font-size: 19px;
    fill: var(--paper);
    text-anchor: middle;
  }
  .school-name {
    font-family: "Roboto", sans-serif;
    font-weight: 700;
    font-size: 17px;
    fill: var(--crimson);
    text-anchor: middle;
  }
  .author-bio {
    font-family: "Crimson Text", serif;
    font-size: 30px;
    fill: var(--paper);
    text-anchor: middle;
  }
  .photo-note {
    font-family: "Crimson Text", serif;
    font-size: 30px;
    fill: var(--ink);
    text-anchor: middle;
  }
</style>
</head>
<body>
<svg class="cover-sheet" viewBox="0 0 2160 1674" preserveAspectRatio="xMidYMid meet" xmlns="http://www.w3.org/2000/svg">
  <defs>
    <filter id="panel-shadow" x="-10%" y="-10%" width="125%" height="125%">
      <feDropShadow dx="-10" dy="12" stdDeviation="10" flood-color="#000" flood-opacity="0.55"/>
    </filter>
    <filter id="shape-shadow" x="-20%" y="-20%" width="140%" height="140%">
      <feDropShadow dx="-6" dy="4" stdDeviation="6" flood-color="#000" flood-opacity="0.5"/>
    </filter>
    <linearGradient id="eye-tones" x1="0" y1="0" x2="1" y2="1">
      <stop offset="0" stop-color="#c9917f"/>
      <stop offset="0.35" stop-color="#8a4b32"/>
      <stop offset="0.6" stop-color="var(--iris-amber)"/>
      <stop offset="0.8" stop-color="var(--iris-green)"/>
      <stop offset="1" stop-color="var(--skin-rose)"/>
    </linearGradient>
  </defs>

  <text class="view-label" x="577" y="132">Front</text>
  <text class="view-label" x="1627" y="145">Back</text>

  <!-- Front cover -->
  <g class="front-cover" transform="translate(97 204)">
    <rect class="front-ground" width="962" height="1244" fill="var(--crimson)" filter="url(#panel-shadow)"/>
    <polygon class="eye-photo-area" role="img" aria-label="Close-up photograph of a human eye with amber-green iris and lashes"
             points="0,396 608,924 0,1176" fill="url(#eye-tones)"/>
    <polygon class="dark-field" points="962,0 77,368 709,880 962,781" fill="var(--charcoal)" filter="url(#shape-shadow)"/>
    <polygon class="grey-wedge" points="753,906 962,822 962,1086" fill="var(--slate)" filter="url(#shape-shadow)"/>
    <polygon class="grey-band" points="0,306 962,1086 962,1231 0,396" fill="var(--slate)" filter="url(#shape-shadow)"/>

    <g class="university-mark">
      <circle cx="155" cy="76" r="46" fill="var(--paper)"/>
      <line x1="39" y1="138" x2="273" y2="138" stroke="var(--paper)" stroke-opacity="0.6" stroke-width="2"/>
      <text class="crest-name" x="156" y="170">Universidad de Montehierro</text>
      <rect x="44" y="188" width="224" height="53" fill="var(--paper)"/>
      <text class="school-name" x="156" y="220">Escuela de Doctorado</text>
    </g>

    <rect class="title-rule" x="561" y="251" width="401" height="5" fill="var(--crimson)"/>
    <text class="thesis-title">
      <tspan x="933" y="304">"Diseño, desarrollo y</tspan>
      <tspan x="933" y="357">validación de una encuesta</tspan>
      <tspan x="933" y="410">para evaluar el compromiso</tspan>
      <tspan x="933" y="463">visual y emocional</tspan>
      <tspan x="933" y="516">subjetivos en pacientes con</tspan>
      <tspan x="933" y="569">Queratocono"</tspan>
    </text>
    <rect class="title-rule" x="561" y="594" width="401" height="5" fill="var(--crimson)"/>
    <text class="university-line" x="936" y="654">Universidad de Montehierro</text>
    <text class="author-name" x="481" y="1178">Iker Zurmendi</text>
  </g>

  <!-- Back cover -->
  <g class="back-cover" transform="translate(1101 204)">
    <rect class="back-ground" width="964" height="1246" fill="var(--charcoal)" filter="url(#panel-shadow)"/>
    <polygon class="crimson-fold" points="0,716 483,1234 964,716 964,1246 0,1246" fill="var(--crimson)"/>
    <text class="author-bio">
      <tspan x="482" y="101">"Iker Zurmendi, MD, es un Oftalmólogo</tspan>
      <tspan x="482" y="135">Subespecialista en Cirugía Refractiva de la</tspan>
      <tspan x="482" y="169">Universidad Tecnológica Cordillerana</tspan>
      <tspan x="482" y="203">(Colombia) y la Universidad de Montehierro</tspan>
      <tspan x="482" y="237">(España). Actualmente se desempeña como</tspan>
      <tspan x="482" y="271">miembro del Departamento de Córnea y</tspan>
      <tspan x="482" y="305">Cirugía Refractiva de la Clínica de</tspan>
      <tspan x="482" y="339">Oftalmología Miraluz y como director de</tspan>
      <tspan x="482" y="373">su propia compañía de emprendimiento</tspan>
      <tspan x="482" y="407">médico Silver Heron Surgical"</tspan>
    </text>
    <rect class="portrait-slot" x="270" y="501" width="422" height="562" rx="40" fill="var(--paper)"/>
    <text class="photo-note" x="481" y="776">Author Photo here</text>
  </g>
</svg>
</body>
</html>
```